Kelvor Engineers: Why you should hire us keepsake

New design. Open to plastic cards. We are an engineering firm that designs cell phone towers and commercial buildings. Please check out our website www.kelvorstruct.com for more details. We want people to remember our card and for it to be useful if possible. We want the same look and feel on these cards to be translated to other marketing material we may need such as brochures.

Target Market(s)

Architects, Developers and Telecommunication Carriers

Industry/Entity Type

Engineering

Contact Information for Business Card

Card with our company colors, logo, and innovative design with elements related to our industry.

Font styles to use
Sans Serif

Colors
9bcb3c
abd036
0255a3

Requirements
Must have
• Sleek and hip design
Nice to have
• Bright lime green and navy coloring that pops with an innovative design.
Should not have
• A basic and boring design

```html
<!DOCTYPE html>
<html lang="en">
<head>
<meta charset="utf-8">
<title>Kelvor Engineers – Business Card</title>
<link rel="stylesheet" href="https://fonts.googleapis.com/css2?family=Roboto+Condensed:wght@700&family=Roboto:wght@400;500;700&display=swap">
<style>
  :root {
    --backdrop: #2b2b2b;
    --navy: #062b58;
    --lime: #1cf70a;
    --paper: #f1f1f1;
    --white: #ffffff;
    --ink-grey: #4a4a4a;
    --rule-navy: #0a2a56;
  }
  * { margin: 0; padding: 0; box-sizing: border-box; }
  html, body { width: 1200px; height: 960px; overflow: hidden; }
  body {
    background: var(--backdrop);
    position: relative;
    font-family: "Roboto", Arial, sans-serif;
  }
  .card {
    position: absolute;
    width: 600px;
    height: 342px;
    overflow: hidden;
  }
  .card-front { left: 314px; top: 113px; background: var(--navy); }
  .card-back  { left: 311px; top: 472px; background: var(--paper); }

  .accent-band { position: absolute; inset: 0; width: 600px; height: 342px; }

  .holder-name {
    position: absolute;
    right: 26px;
    top: 26px;
    font-family: "Roboto Condensed", "Arial Narrow", sans-serif;
    font-weight: 700;
    font-size: 19px;
    color: var(--white);
    letter-spacing: 0.2px;
  }
  .brand-name {
    font-family: "Roboto Condensed", "Arial Narrow", sans-serif;
    font-weight: 700;
    color: var(--lime);
    white-space: nowrap;
  }
  .card-front .brand-name {
    position: absolute;
    left: 36px;
    top: 176px;
    font-size: 36px;
    line-height: 1;
  }
  .contact-block {
    position: absolute;
    left: 38px;
    top: 276px;
    display: flex;
    align-items: center;
    color: var(--white);
    font-size: 14.5px;
  }
  .contact-column { display: flex; flex-direction: column; gap: 4px; }
  .contact-line { display: flex; align-items: center; gap: 9px; line-height: 16px; }
  .contact-line svg { width: 13px; height: 13px; flex: none; }
  .contact-divider {
    width: 1px;
    height: 36px;
    background: var(--white);
    margin: 0 16px 0 16px;
  }

  .card-back .brand-name {
    position: absolute;
    left: 0; right: 0;
    top: 122px;
    text-align: center;
    font-size: 56px;
    line-height: 1;
  }
  .tagline {
    position: absolute;
    left: 0; right: 0;
    top: 266px;
    display: flex;
    justify-content: center;
    align-items: center;
    font-family: "Roboto", Arial, sans-serif;
    font-weight: 700;
    font-size: 15.5px;
    color: var(--lime);
  }
  .tagline::before, .tagline::after {
    content: "";
    width: 30px;
    height: 2px;
    background: var(--rule-navy);
  }
  .office-list {
    position: absolute;
    left: 0; right: 0;
    top: 288px;
    text-align: center;
    font-size: 15px;
    color: var(--ink-grey);
    letter-spacing: 0.9px;
  }
</style>
</head>
<body>
  <section class="card card-front" aria-label="Business card front">
    <svg class="accent-band" viewBox="0 0 600 342" aria-hidden="true">
      <polygon points="0,0 255,0 600,195 600,342" fill="var(--lime)"/>
    </svg>
    <p class="holder-name">DANA WHITLOCK PIERCE</p>
    <p class="brand-name">Kelvor Engineers</p>
    <div class="contact-block">
      <div class="contact-column">
        <span class="contact-line">
          <svg viewBox="0 0 16 16"><path fill="#fff" d="M3.6 1l2.6 3.2-1.5 1.8c.9 2 2.5 3.6 4.5 4.5l1.8-1.5L14.2 11.6 12.9 14.6C6.8 14.2 1.8 9.2 1.4 3.1z"/></svg>
          404.555.0142
        </span>
        <span class="contact-line">
          <svg viewBox="0 0 16 16"><rect x="4" y="1" width="8" height="14" rx="1.5" fill="#fff"/><rect x="5.3" y="3" width="5.4" height="8.5" fill="var(--navy)"/></svg>
          706.555.0198
        </span>
      </div>
      <span class="contact-divider"></span>
      <div class="contact-column">
        <span class="contact-line">
          <svg viewBox="0 0 16 16"><rect x="1" y="3.5" width="14" height="9.5" fill="#fff"/><path d="M1 3.5l7 5.2 7-5.2" fill="none" stroke="var(--navy)" stroke-width="1.2"/></svg>
          dpierce@kelvorstruct.com
        </span>
        <span class="contact-line">
          <svg viewBox="0 0 16 16"><circle cx="8" cy="8" r="6.8" fill="#fff"/><path d="M5 4.5c1.5.5 2 1.8 1 3s.5 2.5 1.8 2.2M10.5 11.5c-.5-1.5.5-2.5 2-2.2" fill="none" stroke="var(--navy)" stroke-width="1.3"/></svg>
          www.kelvorstruct.com
        </span>
      </div>
    </div>
  </section>

  <section class="card card-back" aria-label="Business card back">
    <p class="brand-name">Kelvor Engineers</p>
    <p class="tagline">MULTI-DISCIPLINE ENGINEERING</p>
    <p class="office-list">Northvale | Ridgeport | Calder Bay | Westmere</p>
  </section>
</body>
</html>
```